Need 3 posters for in-store display

Hi Marlene,

Hope you are well.
I need 3 posters for display in my restaurant.

Poster 1: To be print in A1 size vertical
Title: YUMBELLA COMBO $19.50
Choose any Pho OR Noodle Salads
Choose Spring Rolls (5 rolls) OR Ricepaper Rolls (2 rolls)
Choose any Cans OR Water

What I like to see:
- These poster will be place near my counter so I want it to grab customer attention.
- You must use photos to show products
- Make it easy to understand and for customer to follow

Poster 2: To be print in A4 size vertical
Title: ADD TO YOUR ORDER
SpringRolls (Crab / vegetarian) $6 / 5 rolls
Extra Meat $2
Extra Noodles $1
Extra Vegs $1.5
Extra Tofu $2
Extra Crackling $3

Poster 3: To be print in A1 size vertical
Title: FIESTO LOOMA PARTY
Catering Menu Options:
- PHO (Beef, Chicken, Vegan) $12.50 per bowl
- NOODLE SALADS (Beef, Chicken, BBQ Pork, Vegan) $12.50 per bowl
- SpringRolls (Crab / vegetarian) $12.50 for 10 rolls
- Ricepaper Rolls (Prawn, Beef, Chicken, BBQ Pork, Tofu) $12.5 / 5 rolls
- Fried Rice (Prawn, Tofu) $50 per tray (serve 5-6)

Terms & Conditions for All Catering Orders:
1) Minimum orders $200 (Pick-Up from shop Only)
2) All orders must be paid upfront
3) Requires $300 bond for Soup Tank
4) Please give us 48hours notice

• For the YUMBELLA COMBO
• it would be nice to have an image of the battle of water to visually complete the meal deal
• please see attachment of the Crestvale Peak Water

```html
<!DOCTYPE html>
<html lang="en">
<head>
<meta charset="utf-8">
<title>Add to Your Order</title>
<link href="https://fonts.googleapis.com/css2?family=Oswald:wght@500;700&family=Yellowtail&family=Francois+One&display=swap" rel="stylesheet">
<style>
  :root {
    --bg: #1d1d1f;
    --orange: #f39a1e;
    --panel-grey: #3b3c3e;
    --ink-dark: #2e2e30;
    --white: #ffffff;
    --soft: #d9d9d9;
  }
  html, body {
    margin: 0;
    padding: 0;
    overflow: hidden;
    background: var(--bg);
  }
  .poster {
    position: relative;
    width: 849px;
    height: 1200px;
    overflow: hidden;
    background: var(--bg);
    font-family: "Oswald", sans-serif;
  }
  .food-scene {
    position: absolute;
    inset: 0;
  }
  .menu-card {
    position: absolute;
    left: 195px;
    top: 150px;
    width: 462px;
    height: 820px;
    border-radius: 26px 26px 0 0;
    overflow: hidden;
    background: var(--panel-grey);
    box-shadow: 0 10px 40px rgba(0,0,0,.5);
  }
  .menu-card__header {
    position: relative;
    height: 362px;
    background: var(--orange);
    text-align: center;
    color: var(--ink-dark);
  }
  .headline-big {
    position: absolute;
    left: 0; right: 0;
    font-family: "Francois One", sans-serif;
    font-size: 104px;
    line-height: 1;
    letter-spacing: 2px;
    text-shadow: 3px 3px 0 rgba(0,0,0,.18);
  }
  .headline-add { top: 52px; }
  .headline-order { top: 218px; font-size: 96px; }
  .headline-script {
    position: absolute;
    left: 0; right: 0;
    top: 150px;
    font-family: "Yellowtail", cursive;
    font-size: 68px;
    line-height: 1;
  }
  .menu-list {
    list-style: none;
    margin: 0;
    padding: 36px 40px 0 70px;
  }
  .menu-item {
    display: flex;
    align-items: baseline;
    justify-content: space-between;
    height: 48px;
    color: var(--white);
  }
  .menu-item__name {
    font-size: 27px;
    font-weight: 700;
    text-transform: uppercase;
    letter-spacing: 1px;
  }
  .menu-item__name em {
    font-family: "Yellowtail", cursive;
    font-style: normal;
    font-weight: 400;
    text-transform: none;
    font-size: 38px;
    letter-spacing: 0;
    margin-left: 4px;
  }
  .menu-item__price {
    font-size: 38px;
    font-weight: 700;
    color: var(--orange);
    width: 80px;
  }
  .menu-item--lead { height: 40px; }
  .menu-item--lead .menu-item__name em { margin-left: 0; font-size: 42px; }
  .menu-note {
    display: flex;
    justify-content: space-between;
    color: var(--soft);
    font-size: 21px;
    font-weight: 500;
    margin: 0 0 16px;
  }
  .menu-note span:last-child { width: 80px; }
  .brand-badge {
    position: absolute;
    left: 364px;
    top: 915px;
    width: 122px;
    height: 122px;
    border-radius: 50%;
    background: var(--panel-grey);
    border: 4px solid var(--orange);
    display: flex;
    align-items: center;
    justify-content: center;
    text-align: center;
    color: var(--orange);
    font-family: "Oswald", sans-serif;
    font-weight: 700;
    font-size: 22px;
    line-height: 1.05;
    letter-spacing: 1px;
  }
</style>
</head>
<body>
<main class="poster">
  <svg class="food-scene" width="849" height="1200" viewBox="0 0 849 1200" aria-hidden="false">
    <defs>
      <radialGradient id="bowlTop" cx="50%" cy="50%" r="50%">
        <stop offset="0" stop-color="#8a4a2a"/><stop offset=".7" stop-color="#5f7a3a"/><stop offset="1" stop-color="#eeeeee"/>
      </radialGradient>
      <radialGradient id="broth" cx="50%" cy="50%" r="50%">
        <stop offset="0" stop-color="#c9a26a"/><stop offset=".75" stop-color="#7c8d4b"/><stop offset="1" stop-color="#f2f2f2"/>
      </radialGradient>
      <radialGradient id="drink" cx="50%" cy="50%" r="50%">
        <stop offset="0" stop-color="#f4f1e4"/><stop offset="1" stop-color="#c8c3b0"/>
      </radialGradient>
      <radialGradient id="sauce" cx="50%" cy="50%" r="50%">
        <stop offset="0" stop-color="#e2a24a"/><stop offset="1" stop-color="#f3f3f3"/>
      </radialGradient>
      <linearGradient id="board" x1="0" y1="0" x2="1" y2="1">
        <stop offset="0" stop-color="#b98451"/><stop offset="1" stop-color="#8e5e34"/>
      </linearGradient>
    </defs>
    <circle cx="335" cy="60" r="210" fill="url(#bowlTop)" role="img" aria-label="Bowl of grilled meat noodle salad with fresh herbs"/>
    <circle cx="790" cy="30" r="120" fill="url(#drink)" role="img" aria-label="Glass of creamy drink seen from above"/>
    <circle cx="20" cy="370" r="90" fill="url(#sauce)" role="img" aria-label="Small dish of dipping sauce"/>
    <circle cx="95" cy="640" r="230" fill="url(#broth)" role="img" aria-label="Bowl of beef pho with meatballs and herbs"/>
    <rect x="640" y="250" width="240" height="470" rx="10" fill="url(#board)" role="img" aria-label="Fresh rice paper rolls on a wooden board"/>
    <circle cx="790" cy="1020" r="260" fill="url(#broth)" role="img" aria-label="Bowl of chicken pho with coriander and onion"/>
  </svg>

  <section class="menu-card">
    <header class="menu-card__header">
      <div class="headline-big headline-add">ADD</div>
      <div class="headline-script">to your</div>
      <div class="headline-big headline-order">ORDER</div>
    </header>
    <ul class="menu-list">
      <li class="menu-item menu-item--lead">
        <span class="menu-item__name"><em>Springrolls</em></span>
        <span class="menu-item__price">$6</span>
      </li>
      <li class="menu-note"><span>(Crab/Vegetarian)</span><span>5 rolls</span></li>
      <li class="menu-item"><span class="menu-item__name">Extra <em>Meat</em></span><span class="menu-item__price">$2</span></li>
      <li class="menu-item"><span class="menu-item__name">Extra <em>Noodles</em></span><span class="menu-item__price">$1</span></li>
      <li class="menu-item"><span class="menu-item__name">Extra <em>Vegs</em></span><span class="menu-item__price">$1.5</span></li>
      <li class="menu-item"><span class="menu-item__name">Extra <em>Tofu</em></span><span class="menu-item__price">$2</span></li>
      <li class="menu-item"><span class="menu-item__name">Extra <em>Crackling</em></span><span class="menu-item__price">$3</span></li>
    </ul>
  </section>

  <div class="brand-badge">NOODLE<br>NOOK</div>
</main>
</body>
</html>
```